Investment company needing business card

We are wanting a business card which looks sharp and easy on the eye. We are thinking of having a business card with the logo embossed on it, to really make it stand out. We will only have a small amount of information of the business card, person's name, position, email address and phone number

Contact Information for Business Card

Danielle Frost
Executive Assistant
+64 21 473 5162
danielf@harwickpartners.co.nz

Requirements
Must have
• Embossed logo
Should not have
• Not to be busy

```html
<!DOCTYPE html>
<html lang="en">
<head>
<meta charset="utf-8">
<title>Harwick Partners – Business Card</title>
<link href="https://fonts.googleapis.com/css2?family=Exo+2:wght@600;700&family=Open+Sans:wght@400;600&display=swap" rel="stylesheet">
<style>
  :root {
    --canvas: #e9e7e3;
    --card-dark: #141414;
    --card-mid: #262626;
    --brand-green: #22b97c;
    --text-light: #e4e4e4;
    --text-grey: #b8b8b8;
    --rule: #8a8a8a;
  }
  * { margin: 0; padding: 0; box-sizing: border-box; }
  html, body { width: 1200px; height: 960px; overflow: hidden; }
  body {
    background: var(--canvas);
    font-family: "Open Sans", Arial, sans-serif;
    position: relative;
  }
  .card {
    position: absolute;
    left: 290px;
    width: 620px;
    height: 354px;
    background: linear-gradient(160deg, var(--card-mid) 0%, var(--card-dark) 55%, #0e0e0e 100%);
    border-radius: 4px;
    box-shadow: 0 14px 30px rgba(0,0,0,.28);
    color: var(--text-light);
    overflow: hidden;
  }
  .card--front { top: 66px; }
  .card--back { top: 520px; }

  /* front */
  .front-brand {
    position: absolute;
    left: 0; right: 0; top: 110px;
    display: flex; align-items: center; justify-content: center; gap: 18px;
  }
  .brand-square {
    width: 46px; height: 46px;
    background: var(--brand-green);
    border-radius: 3px;
    flex: none;
  }
  .brand-name {
    font-family: "Exo 2", Arial, sans-serif;
    font-weight: 700;
    color: var(--brand-green);
    letter-spacing: 2px;
    text-transform: uppercase;
    white-space: nowrap;
  }
  .front-brand .brand-name { font-size: 40px; }
  .front-url {
    position: absolute;
    left: 0; right: 0; top: 246px;
    text-align: center;
    font-size: 17px;
    letter-spacing: 2.4px;
    color: var(--text-light);
  }

  /* back */
  .back-brand {
    position: absolute;
    left: 112px; top: 56px;
    display: flex; align-items: center; gap: 14px;
  }
  .back-brand .brand-square { width: 38px; height: 38px; }
  .back-brand .brand-name { font-size: 32px; }

  .person {
    position: absolute;
    left: 200px; top: 160px;
    width: 280px;
    text-align: center;
  }
  .person-name {
    font-family: "Exo 2", Arial, sans-serif;
    font-weight: 600;
    font-size: 22px;
    line-height: 30px;
    letter-spacing: 1.5px;
    color: var(--brand-green);
    text-transform: uppercase;
  }
  .person-role {
    font-family: "Exo 2", Arial, sans-serif;
    font-weight: 600;
    font-size: 14px;
    line-height: 20px;
    letter-spacing: 1.6px;
    color: var(--text-grey);
    text-transform: uppercase;
    margin-top: 2px;
  }
  .rule {
    position: absolute;
    height: 1px;
    background: var(--rule);
  }
  .rule--upper { left: 452px; top: 175px; width: 96px; }
  .rule--lower { left: 140px; top: 202px; width: 96px; }

  .contact-row {
    position: absolute;
    display: flex; align-items: center; gap: 22px;
  }
  .contact-row--top { right: 44px; top: 236px; }
  .contact-row--bottom { left: 96px; top: 294px; }
  .contact {
    display: flex; align-items: center; gap: 8px;
    font-size: 14px;
    color: var(--text-light);
    letter-spacing: .3px;
    white-space: nowrap;
  }
  .contact svg { width: 13px; height: 13px; flex: none; }
</style>
</head>
<body>

<section class="card card--front" aria-label="Card front">
  <div class="front-brand">
    <span class="brand-square" aria-hidden="true"></span>
    <span class="brand-name">Harwick Partners</span>
  </div>
  <p class="front-url">www.harwickpartners.com/</p>
</section>

<section class="card card--back" aria-label="Card back">
  <div class="back-brand">
    <span class="brand-square" aria-hidden="true"></span>
    <span class="brand-name">Harwick Partners</span>
  </div>

  <span class="rule rule--upper"></span>
  <div class="person">
    <p class="person-name">Danielle Frost</p>
    <p class="person-role">Executive Assistant</p>
  </div>
  <span class="rule rule--lower"></span>

  <div class="contact-row contact-row--top">
    <p class="contact contact--phone">
      <svg viewBox="0 0 16 16" aria-hidden="true"><circle cx="8" cy="8" r="7.5" fill="var(--brand-green)"/><path d="M5.5 4.5l1.3 1.6-.8 1a5 5 0 002.9 2.9l1-.8 1.6 1.3-.8 1.2c-3.2-.3-6.1-3.2-6.4-6.4z" fill="#111"/></svg>
      +64 21 473 5162
    </p>
    <p class="contact contact--web">
      <svg viewBox="0 0 16 16" aria-hidden="true"><circle cx="8" cy="8" r="7" fill="none" stroke="var(--brand-green)" stroke-width="1.6"/><ellipse cx="8" cy="8" rx="3" ry="7" fill="none" stroke="var(--brand-green)" stroke-width="1.2"/><path d="M1 8h14" stroke="var(--brand-green)" stroke-width="1.2"/></svg>
      www.harwickpartners.com/
    </p>
  </div>
  <div class="contact-row contact-row--bottom">
    <p class="contact contact--email">
      <svg viewBox="0 0 16 16" aria-hidden="true"><rect x="1" y="3.5" width="14" height="9" rx="1" fill="var(--brand-green)"/><path d="M1.5 4l6.5 5 6.5-5" fill="none" stroke="#111" stroke-width="1.2"/></svg>
      danielf@harwickpartners.co.nz
    </p>
  </div>
</section>

</body>
</html>
```